Corporate Business Card

Very professional, Modern, Not to busy, include phone address email, website
(253) 617-4930, 18761 52nd Avenue S, Kent, WA 98047, martin@plumlinegroup.com, varkoworks.com

Target Market(s)

Manufacturing

Industry/Entity Type

Aero, machining, manufacturing, Off road racing

Contact Information for Business Card

Phone, address email, website

```html
<!DOCTYPE html>
<html lang="en">
<head>
<meta charset="utf-8">
<title>Varko Works – Business Card</title>
<link rel="stylesheet" href="https://fonts.googleapis.com/css2?family=Exo+2:wght@400;500;700&display=swap">
<style>
  :root {
    --backdrop: #3a3b3d;
    --paper: #ffffff;
    --navy: #17376e;
    --navy-faint: #21437f;
    --red: #d62631;
    --ink-light: #ffffff;
  }
  * { box-sizing: border-box; margin: 0; padding: 0; }
  html, body { width: 1200px; height: 1015px; overflow: hidden; }
  body {
    background: var(--backdrop);
    font-family: "Exo 2", sans-serif;
    display: flex;
    flex-direction: column;
    align-items: center;
    justify-content: center;
    gap: 56px;
  }
  .card {
    width: 700px;
    height: 400px;
    position: relative;
    box-shadow: 0 10px 30px rgba(0,0,0,0.45);
  }
  .card--front { background: var(--paper); }
  .card--back { background: var(--navy); color: var(--ink-light); }

  .brand {
    position: absolute;
    left: 0; right: 0; top: 150px;
    text-align: center;
  }
  .brand__name {
    font-weight: 700;
    font-size: 64px;
    letter-spacing: 2px;
    color: var(--navy);
    text-transform: uppercase;
    line-height: 1;
  }
  .brand__rule {
    width: 260px;
    height: 2px;
    background: var(--navy);
    margin: 22px auto 0;
  }

  .contact-list {
    position: absolute;
    left: 48px; top: 60px;
    list-style: none;
    font-size: 19px;
    line-height: 1.45;
  }
  .contact-list li, .address {
    display: flex;
    align-items: center;
    gap: 12px;
  }
  .icon { width: 17px; height: 17px; flex: none; fill: var(--red); }
  .address {
    position: absolute;
    left: 48px; bottom: 62px;
    font-size: 19px;
    line-height: 1.35;
  }
  .watermark {
    position: absolute;
    right: 40px; top: 165px;
    text-align: center;
  }
  .watermark__name {
    font-weight: 700;
    font-size: 46px;
    letter-spacing: 2px;
    line-height: 1;
    text-transform: uppercase;
    color: var(--navy-faint);
  }
  .watermark__rule {
    width: 190px;
    height: 2px;
    background: var(--navy-faint);
    margin: 16px auto 0;
  }
</style>
</head>
<body>
  <section class="card card--front">
    <div class="brand">
      <div class="brand__name">Varko Works</div>
      <div class="brand__rule"></div>
    </div>
  </section>

  <section class="card card--back">
    <div class="watermark" aria-hidden="true">
      <div class="watermark__name">Varko Works</div>
      <div class="watermark__rule"></div>
    </div>
    <ul class="contact-list">
      <li>
        <svg class="icon" viewBox="0 0 24 24"><path d="M6.6 10.8a15 15 0 0 0 6.6 6.6l2.2-2.2a1 1 0 0 1 1-.25 11.4 11.4 0 0 0 3.6.57 1 1 0 0 1 1 1V20a1 1 0 0 1-1 1A17 17 0 0 1 3 4a1 1 0 0 1 1-1h3.5a1 1 0 0 1 1 1c0 1.250.2 2.45.57 3.6a1 1 0 0 1-.25 1z"/></svg>
        (253) 617-4930
      </li>
      <li>
        <svg class="icon" viewBox="0 0 24 24"><path d="M2 5h20v14H2z M2 5l10 8 10-8" fill="none" stroke="#d62631" stroke-width="2"/><path d="M2 6l10 7 10-7V5H2z"/></svg>
        martin@plumlinegroup.com
      </li>
      <li>
        <svg class="icon" viewBox="0 0 24 24"><g fill="none" stroke="#d62631" stroke-width="2"><circle cx="12" cy="12" r="9"/><ellipse cx="12" cy="12" rx="4" ry="9"/><path d="M3 12h18M5 7h14M5 17h14"/></g></svg>
        www.varkoworks.com
      </li>
    </ul>
    <div class="address">
      <svg class="icon" viewBox="0 0 24 24"><path d="M12 2a7 7 0 0 0-7 7c0 5 7 13 7 13s7-8 7-13a7 7 0 0 0-7-7zm0 9.5A2.5 2.5 0 1 1 12 6.5a2.5 2.5 0 0 1 0 5z"/></svg>
      <span>18761 52nd Avenue S<br>Kent, WA 98047</span>
    </div>
  </section>
</body>
</html>
```